Wordpress website for Dance Studio

Hi there, I am looking for Wordpress Website for dance studio. Happy for designed to use available themes. Would like a few pages setup and I can do the rest.

Other things I would like included in this theme :

Nice images page OR moving banner
Blog
Ability for youtubes

Other than that, simple requirements, just a gorgeous looking landing page/site etc.

Target Market(s)

Dance mums and kids (dancers)

Industry/Entity Type

Dance and Performancer

Coding

Coded - Design and coding required

Number of Pages Required

4 page

Font styles to use
Sans Serif

Colors
EB3D1F
EC4F4E
F09395
F8D3D4
FCEDEE

Requirements
Must have
• Wordpress theme
Nice to have
• Artistic, graphical, dance studio theme

```html
<!DOCTYPE html>
<html lang="en">
<head>
<meta charset="utf-8">
<title>Little Leap Dance</title>
<link href="https://fonts.googleapis.com/css2?family=Poppins:ital,wght@0,400;0,500;0,600;0,700;1,500&family=Lato:wght@400;700&display=swap" rel="stylesheet">
<style>
:root{
  --red:#eb3d1f;
  --coral:#ec4f4e;
  --rose:#f09395;
  --blush:#f8d3d4;
  --mist:#fcedee;
  --ink:#222222;
  --text:#333333;
  --white:#ffffff;
  --dark:#262422;
}
*{margin:0;padding:0;box-sizing:border-box}
html,body{width:1200px;height:3504px;overflow:hidden;background:var(--white)}
body{position:relative;font-family:'Lato',sans-serif;color:var(--text)}
.abs{position:absolute}
.heading{font-family:'Poppins',sans-serif;font-weight:600;text-transform:uppercase}
.btn{position:absolute;display:flex;align-items:center;justify-content:center;background:var(--coral);color:var(--white);border-radius:30px;font-family:'Poppins',sans-serif;font-weight:600;font-size:15px;text-transform:uppercase}

/* header */
.site-header{left:0;top:0;width:1200px;height:97px;background:var(--white)}
.brand{display:flex;align-items:center;gap:12px}
.brand-dot{width:46px;height:46px;border-radius:50%;background:var(--coral)}
.brand-name{font-family:'Poppins',sans-serif;font-weight:500;font-size:22px;line-height:26px;color:var(--ink);text-transform:uppercase}
.nav a{position:absolute;top:40px;font-family:'Poppins',sans-serif;font-size:15px;color:var(--ink);text-decoration:none;text-transform:uppercase}
.nav .active::after{content:"";position:absolute;left:0;right:0;bottom:-10px;height:2px;background:var(--coral)}

/* hero */
.hero-photo{left:0;top:97px;width:1200px;height:660px;background:radial-gradient(circle at 30% 30%,#4a3a8e 0%,transparent 50%),radial-gradient(circle at 80% 60%,#a0265e 0%,transparent 45%),linear-gradient(180deg,#1f2a63 0%,#3a2660 55%,#2a1e3a 100%)}
.hero-title{left:108px;top:268px;font-family:'Poppins',sans-serif;font-weight:700;font-size:52px;line-height:65px;color:var(--white);text-transform:uppercase}
.hero-copy{left:110px;top:398px;width:470px;font-size:15px;line-height:26px;color:var(--white)}
.hero-curve{left:0;top:600px}
.dots{left:577px;top:707px;display:flex;gap:6px;align-items:center}
.dots span{width:10px;height:10px;border-radius:50%;background:var(--white)}
.dots .on{width:14px;height:14px;background:var(--coral);border:2px solid var(--white)}

/* about */
.about-frame{left:86px;top:861px;width:488px;height:357px;border-left:3px solid var(--red);border-bottom:3px solid var(--red)}
.about-frame::before{content:"";position:absolute;left:0;top:0;width:26px;height:3px;background:var(--red)}
.about-frame::after{content:"";position:absolute;right:0;bottom:0;width:3px;height:26px;background:var(--red)}
.about-photo{left:112px;top:835px;width:488px;height:357px;background:linear-gradient(135deg,#e6e9ec 0%,#b9c3c9 45%,#7e9a7c 75%,#a9b7c7 100%)}
.section-title{font-size:30px;color:var(--ink)}
.section-title em{font-style:normal;color:var(--coral)}
.about-copy{left:673px;top:889px;width:420px;font-size:15px;line-height:26px;color:var(--text)}

/* blog */
.blog{left:0;top:1303px;width:1200px;height:720px;background:radial-gradient(circle at 20% 30%,#4a4038 0%,transparent 45%),radial-gradient(circle at 80% 40%,#4a423a 0%,transparent 45%),linear-gradient(180deg,#2a2724,#1f1d1b)}
.blog-title{left:0;top:1377px;width:1200px;text-align:center;font-size:33px;color:var(--white)}
.post-photo{width:363px;height:278px;border:5px solid var(--coral)}
.tab{position:absolute;height:37px;background:var(--coral);color:var(--white);display:flex;align-items:center;justify-content:center;gap:6px;clip-path:polygon(0 0,100% 0,100% 100%,0 100%,18px 50%)}
.tab .day{font-family:'Poppins',sans-serif;font-weight:600;font-size:24px}
.tab .mon{font-family:'Poppins',sans-serif;font-size:11px;line-height:12px;text-align:center}
.tab .count{font-size:15px}
.post-title{font-family:'Poppins',sans-serif;font-weight:600;font-size:27px;color:var(--white)}
.post-copy{width:370px;font-size:15px;line-height:26px;color:#e6e6e6}

/* newsletter */
.news-title{left:0;top:2100px;width:1200px;text-align:center;font-size:35px;color:var(--ink)}
.news-field{left:290px;top:2205px;width:620px;height:64px;border-radius:32px;background:#e6e6e6}
.news-field .placeholder{position:absolute;left:60px;top:24px;font-family:'Poppins',sans-serif;font-size:12px;color:#666;text-transform:uppercase}
.news-field svg{position:absolute;left:26px;top:24px}
.news-btn{left:718px;top:2205px;width:192px;height:64px;border-radius:32px;font-size:19px}
.news-note{left:0;top:2296px;width:1200px;text-align:center;font-size:15px;color:var(--text)}

/* video */
.video-band{left:0;top:2400px;width:1200px;height:341px;background:linear-gradient(180deg,#ef6a66,var(--coral))}
.video-frame{left:112px;top:2513px;width:976px;height:469px;border:7px solid var(--white);box-shadow:0 8px 24px rgba(0,0,0,.18)}
.video-still{width:100%;height:100%;background:linear-gradient(135deg,#6b6460 0%,#8a7f7a 40%,#7b6c6e 70%,#5a5250 100%)}
.play{left:553px;top:2703px;width:96px;height:96px;border-radius:50%;background:var(--red);box-shadow:0 0 0 14px rgba(235,61,31,.35);display:flex;align-items:center;justify-content:center}
.video-caption{left:0;top:2866px;width:1200px;text-align:center;font-family:'Poppins',sans-serif;font-style:italic;font-weight:500;font-size:29px;color:var(--white)}

/* footer */
.footer-brand{left:0;top:3082px;width:1200px;display:flex;justify-content:center}
.col-title{font-family:'Poppins',sans-serif;font-weight:500;font-size:21px;color:var(--coral);text-transform:uppercase}
.col-list{list-style:none;font-size:15px;line-height:26px;color:var(--ink);text-transform:uppercase}
.contact-item{display:flex;gap:12px;font-size:15px;line-height:26px;color:var(--ink)}
.contact-item svg{flex:none;margin-top:6px}
.footer-rule{left:110px;top:3411px;width:980px;height:1px;background:#cfcfcf}
.copyright{left:110px;top:3441px;font-size:15px;color:var(--ink)}
.social{left:946px;top:3440px;display:flex;gap:22px}
.social span{width:20px;height:20px;border-radius:50%;background:var(--coral)}
</style>
</head>
<body>

<header class="site-header abs">
  <div class="brand abs" style="left:113px;top:22px">
    <span class="brand-dot"></span>
    <span class="brand-name">Little Leap<br>Dance</span>
  </div>
  <nav class="nav">
    <a class="active" style="left:469px">Home</a>
    <a style="left:544px">About Us</a>
    <a style="left:650px">Our Video</a>
    <a style="left:765px">Blog</a>
    <a style="left:835px">Contact Us</a>
  </nav>
  <a class="btn" style="left:960px;top:29px;width:128px;height:43px">Log In</a>
</header>

<section class="hero">
  <div class="hero-photo abs" role="img" aria-label="Children dancing under colourful disco lights in a studio"></div>
  <h1 class="hero-title abs">Little Leap<br>Dance</h1>
  <p class="hero-copy abs">Dance Studio in Australia lorem ipsum dolor sit amet, consectetur adipiscing elit, sed do eiusmod tempo</p>
  <a class="btn" style="left:110px;top:471px;width:136px;height:42px">Get Started</a>
  <svg class="hero-curve abs" width="1200" height="160" viewBox="0 0 1200 160">
    <path d="M0 34 Q600 264 1200 34 L1200 160 L0 160Z" fill="#ffffff"/>
    <path d="M0 30 Q600 262 1200 30" fill="none" stroke="#eb3d1f" stroke-width="9"/>
  </svg>
  <div class="dots abs"><span></span><span class="on"></span><span></span></div>
</section>

<section class="about">
  <div class="about-frame abs"></div>
  <div class="about-photo abs" role="img" aria-label="Mother and daughter dancing together in a bright living room"></div>
  <h2 class="section-title heading abs" style="left:673px;top:830px">About <em>Us</em></h2>
  <p class="about-copy abs">Lorem ipsum dolor sit amet, consectetur adipiscing elit, sed do eiusmod tempor incididunt ut labore et dolore magna aliqua. Ut enim ad minim veniam, quis nostrud exercitation ullamco laboris nisi ut aliquip ex ea commodo consequat. Duis aute irure dolor in reprehenderit in voluptate velit esse cillum dolore eu fugiat nulla pariatur. Excepteur sint occaecat cupidatat non proident, sunt in culpa qui officia deserunt mollit anim id est laborum.</p>
  <a class="btn" style="left:675px;top:1127px;width:136px;height:42px">Learn More</a>
</section>

<section class="blog abs" role="img" aria-label="Dim background photo of dancers in class"></section>
<h2 class="blog-title heading abs">Recent Blog</h2>

<article>
  <div class="post-photo abs" style="left:220px;top:1462px" role="img" aria-label="Young ballet students stretching at the barre"></div>
  <div class="tab" style="left:117px;top:1529px;width:101px"><span class="day">09</span><span class="mon">Nov<br>2021</span></div>
  <div class="tab" style="left:141px;top:1584px;width:77px"><span class="count">0</span>
    <svg width="18" height="16" viewBox="0 0 18 16"><path d="M2 2h14v9H8l-4 3v-3H2z" fill="none" stroke="#fff" stroke-width="1.6"/></svg></div>
  <div class="tab" style="left:166px;top:1637px;width:52px">
    <svg width="16" height="13" viewBox="0 0 16 13"><rect x="1" y="1" width="14" height="11" fill="none" stroke="#fff" stroke-width="1.5"/><path d="M2 11l4-5 3 3 2-2 3 4z" fill="#fff"/></svg></div>
  <h3 class="post-title abs" style="left:216px;top:1758px">Sed ut Perspiciatis Unde</h3>
  <p class="post-copy abs" style="left:218px;top:1809px">Lorem ipsum dolor sit amet, consectetur adipiscing elit, sed do eiusmod tempor incididunt ut labore et dolore magna aliqua.</p>
  <a class="btn" style="left:218px;top:1910px;width:128px;height:42px">Read More</a>
</article>

<article>
  <div class="post-photo abs" style="left:724px;top:1462px" role="img" aria-label="Group of children practising in a bright dance studio"></div>
  <div class="tab" style="left:622px;top:1529px;width:101px"><span class="day">09</span><span class="mon">Nov<br>2021</span></div>
  <div class="tab" style="left:646px;top:1584px;width:77px"><span class="count">0</span>
    <svg width="18" height="16" viewBox="0 0 18 16"><path d="M2 2h14v9H8l-4 3v-3H2z" fill="none" stroke="#fff" stroke-width="1.6"/></svg></div>
  <div class="tab" style="left:671px;top:1637px;width:52px">
    <svg width="16" height="13" viewBox="0 0 16 13"><rect x="1" y="1" width="14" height="11" fill="none" stroke="#fff" stroke-width="1.5"/><path d="M2 11l4-5 3 3 2-2 3 4z" fill="#fff"/></svg></div>
  <h3 class="post-title abs" style="left:721px;top:1758px">Sed ut Perspiciatis Unde</h3>
  <p class="post-copy abs" style="left:723px;top:1809px">Lorem ipsum dolor sit amet, consectetur adipiscing elit, sed do eiusmod tempor incididunt ut labore et dolore magna aliqua.</p>
  <a class="btn" style="left:723px;top:1910px;width:128px;height:42px">Read More</a>
</article>

<section class="newsletter">
  <h2 class="news-title section-title heading abs">Subscribe Our <em>Newsletter</em></h2>
  <div class="news-field abs">
    <svg width="20" height="15" viewBox="0 0 20 15"><rect x="1" y="1" width="18" height="13" fill="none" stroke="#777" stroke-width="1.4"/><path d="M1 1l9 7 9-7" fill="none" stroke="#777" stroke-width="1.4"/></svg>
    <span class="placeholder">Your Email Address</span>
  </div>
  <a class="btn news-btn">Submit Now</a>
  <p class="news-note abs">Sign Up to Receive Our Latest News Directly in Your Ball</p>
</section>

<section class="video">
  <div class="video-band abs" role="img" aria-label="Faint photo of dancers over a coral band"></div>
  <div class="video-frame abs"><div class="video-still" role="img" aria-label="Children dancing together in a studio class"></div></div>
  <div class="play abs"><svg width="30" height="32" viewBox="0 0 30 32"><path d="M6 3l22 13L6 29z" fill="#fff"/></svg></div>
  <p class="video-caption abs">Watch our Video</p>
</section>

<footer>
  <div class="footer-brand abs"><div class="brand"><span class="brand-dot"></span><span class="brand-name">Little Leap<br>Dance</span></div></div>

  <h4 class="col-title abs" style="left:146px;top:3196px">Links</h4>
  <ul class="col-list abs" style="left:146px;top:3248px">
    <li>Home</li><li>About Us</li><li>Blog</li><li>Our Video</li><li>Contact Us</li>
  </ul>

  <h4 class="col-title abs" style="left:457px;top:3196px">Contact Us</h4>
  <div class="abs" style="left:459px;top:3248px;width:280px">
    <div class="contact-item"><svg width="13" height="16" viewBox="0 0 13 16"><path d="M6.5 0A6 6 0 0 0 .5 6c0 4.5 6 10 6 10s6-5.5 6-10a6 6 0 0 0-6-6z" fill="#222"/><circle cx="6.5" cy="6" r="2.2" fill="#fff"/></svg><span>123,Lorem ipsum dolor sit amet, consectetur adipiscing elit.</span></div>
    <div class="contact-item" style="margin-top:10px"><svg width="14" height="14" viewBox="0 0 14 14"><path d="M3 0l3 3-2 2c1 2 3 4 5 5l2-2 3 3-2 3C6 14 0 8 0 3z" fill="#222"/></svg><span>(888) 888 8888</span></div>
    <div class="contact-item" style="margin-top:8px"><svg width="14" height="11" viewBox="0 0 14 11"><rect width="14" height="11" fill="#222"/><path d="M0 0l7 6 7-6" fill="none" stroke="#fff" stroke-width="1.2"/></svg><span>info@littleleapdance.com</span></div>
  </div>

  <h4 class="col-title abs" style="left:895px;top:3196px">Our Company</h4>
  <ul class="col-list abs" style="left:896px;top:3248px">
    <li>Terms&amp;Condtions</li><li>Privacy Polict</li><li>About Us</li><li>Support</li>
  </ul>

  <div class="footer-rule abs"></div>
  <p class="copyright abs">©COPYRIGHTS 2021 COMPANY NAME &nbsp;| &nbsp;&nbsp;ALL RIGHTS RESERVED</p>
  <div class="social abs" aria-label="Social links"><span></span><span></span><span></span><span></span></div>
</footer>

</body>
</html>
```